Heritage Hollow Business Cards

Require a business card design. <br/><br/>Needs to include logo (either round or long version) plus these details:<br/>Maya Torvell<br/>Heritage Hollow<br/>maya@kelvadtrading.com.au<br/>02 6481 7395<br/>PO Box Glenwarra NSW 2791<br/>www.heritagehollow.com.au<br/><br/>I need in an editable format so that I can create for multiple staff members. <br/><br/>

Target Market(s)

We are an online store selling renovation products to home owners are builders. Looking for a classic classy design.

Industry/Entity Type

Home And Garden

Contact Information for Business Card

Maya Torvell
Heritage Hollow
maya@kelvadtrading.com.au
02 6481 7395
PO Box Glenwarra NSW 2791
www.heritagehollow.com.au

Colors

Designer to choose colors to be used in the design.

Requirements
Must have
• Must include Logo.

```html
<!DOCTYPE html>
<html lang="en">
<head>
<meta charset="utf-8">
<title>Heritage Hollow Business Cards</title>
<link rel="stylesheet" href="https://fonts.googleapis.com/css2?family=Lora:wght@400;700&display=swap">
<style>
  :root {
    --backdrop: #2e2e2e;
    --card: #ffffff;
    --ink: #2a2a2a;
    --charcoal: #2b2a2a;
    --swoosh-black: #1c1c1c;
    --swoosh-grey: #a9a9a9;
    --muted: #9a9a9a;
    --on-dark: #f2f2f2;
  }
  * { box-sizing: border-box; margin: 0; padding: 0; }
  html, body { width: 1200px; height: 880px; overflow: hidden; }
  body {
    background: var(--backdrop);
    font-family: "Lora", Georgia, serif;
    display: flex;
    align-items: center;
    justify-content: center;
    gap: 40px;
  }
  .card {
    position: relative;
    width: 540px;
    height: 310px;
    background: var(--card);
    border-radius: 18px;
    overflow: hidden;
    box-shadow: 0 10px 30px rgba(0,0,0,.45);
  }
  .brand {
    position: absolute;
    display: flex;
    align-items: center;
    gap: 10px;
    color: var(--ink);
    font-weight: 700;
    white-space: nowrap;
  }
  .brand-mark {
    border: 2px solid var(--ink);
    border-radius: 50%;
    flex: none;
  }
  .card-front .brand { left: 50%; top: 50%; transform: translate(-50%, -50%); font-size: 38px; }
  .card-front .brand-mark { width: 64px; height: 64px; }
  .card-back .brand { left: 24px; top: 92px; font-size: 28px; }
  .card-back .brand-mark { width: 48px; height: 48px; }
  .swoosh { position: absolute; inset: 0; width: 100%; height: 100%; }
  .holder { position: absolute; right: 30px; top: 20px; text-align: right; }
  .holder-name { font-size: 20px; color: var(--ink); }
  .holder-role { font-size: 12px; color: var(--muted); margin-top: 2px; }
  .contacts {
    position: absolute;
    right: 20px;
    top: 176px;
    list-style: none;
    color: var(--on-dark);
    font-size: 12px;
    text-align: right;
  }
  .contacts li {
    display: flex;
    align-items: center;
    justify-content: flex-end;
    gap: 7px;
    height: 21px;
  }
  .contacts svg { width: 15px; height: 15px; flex: none; }
</style>
</head>
<body>

  <section class="card card-front" aria-label="Card front">
    <div class="brand"><span class="brand-mark"></span>Heritage Hollow</div>
  </section>

  <section class="card card-back" aria-label="Card back">
    <svg class="swoosh" viewBox="0 0 540 310" preserveAspectRatio="none" aria-hidden="true">
      <path fill="var(--swoosh-grey)" d="M0,290 C110,284 210,268 250,212 C240,262 160,294 0,304 Z"/>
      <path fill="var(--swoosh-black)" d="M80,310 C180,300 230,285 245,255 C268,210 285,165 312,135 C350,95 430,75 525,72 C430,80 372,110 330,142 C300,172 280,222 260,264 C248,292 228,306 195,310 Z"/>
      <path fill="var(--charcoal)" d="M540,80 C440,85 380,115 340,150 C310,180 290,230 270,270 C258,295 240,310 210,310 L540,310 Z"/>
    </svg>

    <div class="holder">
      <p class="holder-name">Maya Torvell</p>
      <p class="holder-role">Managing Director</p>
    </div>

    <div class="brand"><span class="brand-mark"></span>Heritage Hollow</div>

    <ul class="contacts">
      <li>02 6481 7395
        <svg viewBox="0 0 16 16" aria-hidden="true"><circle cx="8" cy="8" r="7" fill="none" stroke="currentColor"/><path d="M5.5 4.5l1.5 0 .6 1.8-1 .8a5 5 0 0 0 2.3 2.3l.8-1 1.8.6v1.5c-3.5.3-6.3-2.5-6-6z" fill="currentColor"/></svg>
      </li>
      <li>maya@kelvadtrading.com.au
        <svg viewBox="0 0 16 16" aria-hidden="true"><circle cx="8" cy="8" r="7" fill="none" stroke="currentColor"/><rect x="4.5" y="5.5" width="7" height="5" fill="none" stroke="currentColor" stroke-width=".9"/><path d="M4.5 5.5l3.5 3 3.5-3" fill="none" stroke="currentColor" stroke-width=".9"/></svg>
      </li>
      <li>PO Box Glenwarra NSW 2791
        <svg viewBox="0 0 16 16" aria-hidden="true"><circle cx="8" cy="8" r="7" fill="none" stroke="currentColor"/><path d="M8 12.5s-3-3-3-5.2a3 3 0 0 1 6 0c0 2.2-3 5.2-3 5.2z" fill="currentColor"/><circle cx="8" cy="7.3" r="1.1" fill="var(--charcoal)"/></svg>
      </li>
      <li>www.heritagehollow.com.au
        <svg viewBox="0 0 16 16" aria-hidden="true"><circle cx="8" cy="8" r="7" fill="none" stroke="currentColor"/><circle cx="8" cy="8" r="4" fill="none" stroke="currentColor" stroke-width=".9"/><path d="M4 8h8M8 4c-2 2.5-2 5.5 0 8M8 4c2 2.5 2 5.5 0 8" fill="none" stroke="currentColor" stroke-width=".8"/></svg>
      </li>
    </ul>
  </section>

</body>
</html>
```